New Business Cards for Tormin Group

We need a new Business Card to compliment our new logo. We are a vibrant design, manufacture and install business providing recreation areas, public parks and Municipal spaces. We want business cards that are classy, modern and clean.

We have recently changed our logo, and are celebrating our 40th anniversary. We want business cards with a new modern design to reflect our status.

Target Market(s)

Customers

Contact Information for Business Card

We need all the details of our 3 offices as per the business card attached. Please disregard the old logo on the business card, the other three files show our new logo.

Requirements
Must have
• All info as per attached business card but with new logo.
Nice to have

```html
<!DOCTYPE html>
<html lang="en">
<head>
<meta charset="utf-8">
<title>Tormin Group – Business Card</title>
<link rel="stylesheet" href="https://fonts.googleapis.com/css2?family=Montserrat:wght@500;600;700&family=Open+Sans:wght@400;600&display=swap">
<style>
  :root {
    --backdrop: #5e5e5e;
    --card: #ffffff;
    --brand-red: #e8303a;
    --ink: #333333;
    --ink-soft: #666666;
    --box: #e9eaec;
    --box-ink: #555555;
    --band-dark: #4a4a4c;
    --band-grey: #5f5f61;
  }
  * { margin: 0; padding: 0; box-sizing: border-box; }
  html, body { width: 1200px; height: 1200px; overflow: hidden; }
  body {
    background: var(--backdrop);
    font-family: "Open Sans", Arial, sans-serif;
    position: relative;
  }
  .card {
    position: absolute;
    left: 136px; top: 368px;
    width: 926px; height: 540px;
    background: var(--card);
    border-radius: 34px;
    overflow: hidden;
  }
  .person { position: absolute; left: 30px; top: 62px; }
  .person__name {
    font-family: "Montserrat", Arial, sans-serif;
    font-weight: 700; font-size: 26px; color: var(--brand-red);
    letter-spacing: 0.2px;
  }
  .person__title { margin-top: 10px; font-size: 20px; color: var(--ink); }
  .person__contact { margin-top: 14px; font-size: 19px; line-height: 36px; color: var(--ink-soft); }
  .person__contact .label { color: var(--ink); }

  .brand {
    position: absolute; right: 42px; top: 74px;
    display: flex; align-items: center; gap: 14px;
  }
  .brand__dot { width: 64px; height: 64px; border-radius: 50%; background: var(--brand-red); }
  .brand__name {
    font-family: "Montserrat", Arial, sans-serif;
    font-weight: 700; font-size: 34px; color: var(--band-dark);
  }

  .office { position: absolute; top: 304px; }
  .office__heading {
    font-family: "Montserrat", Arial, sans-serif;
    font-weight: 600; font-size: 21px; color: var(--brand-red);
    margin-left: 4px; margin-bottom: 12px;
  }
  .office__details {
    background: var(--box);
    padding: 6px 4px 5px;
    font-size: 16px; line-height: 28px; color: var(--box-ink);
    white-space: nowrap;
  }
  .office--head { left: 26px; }
  .office--head .office__details { width: 275px; }
  .office--dubai { left: 335px; }
  .office--dubai .office__details { width: 259px; }
  .office--qatar { left: 636px; }
  .office--qatar .office__details { width: 248px; margin-top: 2px; }

  .footer-bands { position: absolute; left: 0; top: 0; width: 926px; height: 540px; }
  .website {
    position: absolute; left: 30px; top: 498px;
    font-size: 19px; color: #ffffff;
  }
</style>
</head>
<body>
  <div class="card">
    <div class="person">
      <div class="person__name">Sami Hadrawi</div>
      <div class="person__title">Managing Partner</div>
      <div class="person__contact">
        <div><span class="label">Phone:</span> +971 (0)50 000 4817</div>
        <div><span class="label">Email:</span> sami@tormingroup.com</div>
      </div>
    </div>

    <div class="brand">
      <span class="brand__dot"></span>
      <span class="brand__name">Tormin Group</span>
    </div>

    <section class="office office--head">
      <h3 class="office__heading">Head Office</h3>
      <div class="office__details">
        P.O. Box: 41208 Abu Dhabi. U.A.E<br>
        Tel No: +971 (0)2 5550184<br>
        Fax No: +971(0)2 5550185<br>
        Email: sales@tormingroup.com
      </div>
    </section>

    <section class="office office--dubai">
      <h3 class="office__heading">Dubai Office</h3>
      <div class="office__details">
        P.O. Box: 208731 Dubai, U.A.E<br>
        Tel No: +971 (0)4 555120<br>
        Fax No: +971(0)4 555129<br>
        Email: sales@tormingroup.com
      </div>
    </section>

    <section class="office office--qatar">
      <h3 class="office__heading">Qater Office</h3>
      <div class="office__details">
        P.O. Box: 30672 Doha, Qatter<br>
        Tel No: +974 44055310<br>
        Fax No: +971 44055311<br>
        Email: sales@tormingroup.com
      </div>
    </section>

    <svg class="footer-bands" viewBox="0 0 926 540" aria-hidden="true">
      <path d="M0 491 L268 491 Q281 491 288 500 L318 540 L0 540 Z" fill="var(--brand-red)"/>
      <path d="M297 505 L578 505 Q596 505 605 518 L618 540 L327 540 Z" fill="var(--band-dark)"/>
      <path d="M610 521 L926 521 L926 540 L624 540 Z" fill="var(--band-grey)"/>
    </svg>
    <div class="website">www.tormingroup.com</div>
  </div>
</body>
</html>
```